Vertical Banner

I need an eye-catching banner created for street fairs, indoor and outdoor events to draw attention to our language school. It will be to print on this banner (specs included):
https://www.banvoxprint.com/tag/617/Retractable-Banners/product/5174-46/Economy-Retractor-Banner-Display-27-09

I want the banner to be:
- SIMPLE
- Eye catching (not busy with too many pictures or information)
- It should say at top prominently: "Come learn a language!" and have our name.
- Below these languages should be large and eye-catching: Spanish, Chinese, French, Russian, German, Italian, Farsi, Turkish, Portuguese, ASL, Cantonese, Japanese, Korean, Vietnamese, Arabic, Dutch, more... (if some need to be cut our because of overcrowding let me know OR we can make some big and others small)
- Below this it should have GROUP & PRIVATE LESSONS
- It should be colorful and make people think of things international - perhaps national flags in background? Or images of world famous monuments? Could be image of adutls in a classroom. Sth that gets people excited about travel and language learning
- It should have our contact info VERY large at bottom:
Tovira Languages -
San Francisco, Silicon Valley & New York City
www.toviralanguagesf.com
415-629-5140
info@toviralanguagesf.com
(this can be smaller)
Four Wexmoor Plaza
Lobby 3
San Francisco, CA 94187

Hey Designers, please feel free to do a rough take on it. I don't need you to spend too much time, just give me a general idea of how you would make it look, then i know we can go from there later and refine it. Feel free to make it more of a quick sketch to show how you would do it.

Target Market(s)

adults from about 25-55 years old, educated, employed and typically world travellers

Industry/Entity Type

School

Colors
86cfc6
00a990
cadf82
acd036
9bcb3c
fbed22
f78f20
ffc214
f37122

Requirements
Must have
• Must be simple! Too many banners put way too much information and pictures. I want someone to walk by and immediately know we teach foreign languages. Must have bright colors and large font for languages offered
Should not have
• Should not be too full of images and design that distract the viewer from seeing the main thing I want them to see: that we teacher languages

```html
<!DOCTYPE html>
<html lang="en">
<head>
<meta charset="utf-8">
<title>Tovira Languages – Retractable Banner</title>
<link href="https://fonts.googleapis.com/css2?family=Anton&family=Roboto+Condensed:wght@400;700&family=Yellowtail&display=swap" rel="stylesheet">
<style>
  :root {
    --backdrop: #d6d8db;
    --paper: #ffffff;
    --brand-green: #5db12f;
    --headline-red: #e3101b;
    --accent-yellow: #ffd500;
    --ribbon-shadow: #4a4a4a;
    --contact-grey: #e6e5e7;
    --ink: #141414;
    --book-tan: #c9ab78;
  }
  * { margin: 0; padding: 0; box-sizing: border-box; }
  html, body {
    width: 1200px; height: 1175px; overflow: hidden;
    background: var(--backdrop);
  }
  .banner {
    position: absolute; left: 390px; top: 20px;
    width: 420px; height: 1135px;
    background: var(--paper);
    overflow: hidden;
    box-shadow: 0 6px 24px rgba(0,0,0,.18);
  }
  .brand-name {
    position: absolute; top: 62px; left: 0; width: 100%;
    text-align: center;
    font-family: "Roboto Condensed", sans-serif;
    font-weight: 700; font-size: 60px; line-height: 1;
    color: var(--brand-green);
    letter-spacing: -1px;
  }
  .brand-stripes {
    position: absolute; top: 150px; left: 0; width: 100%; height: 40px;
  }
  .headline {
    position: absolute; top: 222px; left: 0; width: 100%;
    text-align: center;
    font-family: "Anton", sans-serif;
    color: var(--headline-red);
    text-transform: uppercase;
    line-height: .98;
  }
  .headline .line-small { display: block; font-size: 62px; }
  .headline .line-large { display: block; font-size: 80px; }
  .language-list {
    position: absolute; top: 428px; left: 0; width: 100%;
    list-style: none; text-align: center;
    font-family: "Roboto Condensed", sans-serif;
    font-weight: 700; font-size: 23px;
    color: var(--brand-green);
  }
  .language-list li { height: 41px; line-height: 41px; }
  .language-list .sep { color: var(--headline-red); font-weight: 400; margin: 0 5px; }
  .language-list .dots { color: var(--headline-red); }
  .lessons-ribbon {
    position: absolute; top: 622px; left: 14px; width: 392px; height: 84px;
  }
  .lessons-ribbon svg { position: absolute; inset: 0; }
  .lessons-ribbon span {
    position: absolute; left: 0; right: 0; top: 20px;
    text-align: center;
    font-family: "Yellowtail", cursive;
    font-size: 34px; color: var(--accent-yellow);
    transform: rotate(-3.5deg);
  }
  .landmarks-art {
    position: absolute; top: 716px; left: 0; width: 100%; height: 186px;
    background: linear-gradient(180deg, #ffffff 0%, #eeeeee 55%, #e2d2b0 78%, var(--book-tan) 92%, #6f5a3a 100%);
  }
  .contact-block {
    position: absolute; top: 902px; left: 0; width: 100%; height: 233px;
    background: var(--contact-grey);
    text-align: center;
    font-family: "Roboto Condensed", sans-serif;
    font-weight: 700; color: var(--ink);
  }
  .contact-block .regions { margin-top: 14px; font-size: 21px; }
  .contact-block .phone-web { margin-top: 6px; font-size: 21px; }
  .contact-block .phone-web .item { white-space: nowrap; }
  .contact-block .phone-web .item + .item { margin-left: 12px; }
  .contact-block svg.icon { width: 15px; height: 15px; vertical-align: -1px; margin-right: 4px; }
  .contact-block .email { margin-top: 4px; font-size: 17px; font-weight: 400; }
  .contact-block .address { margin-top: 6px; font-size: 22px; line-height: 1.15; }
  .bottom-wave { position: absolute; left: 0; bottom: 0; width: 420px; height: 110px; }
</style>
</head>
<body>
  <main class="banner">
    <h1 class="brand-name">Tovira Languages</h1>

    <svg class="brand-stripes" viewBox="0 0 420 40" preserveAspectRatio="none" aria-hidden="true">
      <rect x="0" y="0" width="420" height="12" fill="var(--headline-red)"/>
      <rect x="0" y="14" width="420" height="10" fill="var(--accent-yellow)"/>
      <rect x="0" y="26" width="420" height="12" fill="var(--headline-red)"/>
    </svg>

    <h2 class="headline">
      <span class="line-small">Come learn a</span>
      <span class="line-large">Language!</span>
    </h2>

    <ul class="language-list">
      <li>Spanish<span class="sep">|</span>Chinese<span class="sep">|</span>French<span class="sep">|</span>Russian</li>
      <li>German<span class="sep">|</span>Italian<span class="sep">|</span>Farsi<span class="sep">|</span>Turkish<span class="sep">|</span>ASL</li>
      <li>Portuguese<span class="sep">|</span>Cantonese<span class="sep">|</span>Japanese</li>
      <li>Korean<span class="sep">|</span>Arabic<span class="sep">|</span>Dutch</li>
      <li>Vietnamese<span class="sep">|</span>more<span class="dots">...</span></li>
    </ul>

    <div class="lessons-ribbon">
      <svg viewBox="0 0 392 84" aria-hidden="true">
        <polygon points="6,58 376,8 386,18 14,72" fill="var(--ribbon-shadow)"/>
        <polygon points="0,32 382,8 370,30 388,52 6,76 18,54" fill="var(--headline-red)"/>
      </svg>
      <span>Group &amp; Private Lessons</span>
    </div>

    <div class="landmarks-art" role="img" aria-label="Line drawing of world landmarks — Eiffel Tower, Statue of Liberty, Leaning Tower of Pisa, Taj Mahal, pyramids and a pagoda — rising from an open book"></div>

    <section class="contact-block">
      <p class="regions">San Francisco, Silicon Valley &amp; New York City</p>
      <p class="phone-web">
        <span class="item"><svg class="icon" viewBox="0 0 16 16" aria-hidden="true"><circle cx="8" cy="8" r="8" fill="var(--ink)"/><path d="M5.2 4.2l1.6-.2.8 2-1 .8c.5 1 1.3 1.8 2.3 2.3l.8-1 2 .8-.2 1.6c-3.4.2-6.5-2.9-6.3-6.3z" fill="#fff"/></svg>415-629-5140</span>
        <span class="item"><svg class="icon" viewBox="0 0 16 16" aria-hidden="true"><g fill="none" stroke="var(--ink)" stroke-width="1.3"><circle cx="8" cy="8" r="7"/><ellipse cx="8" cy="8" rx="3" ry="7"/><line x1="1" y1="8" x2="15" y2="8"/></g></svg>www.toviralanguagesf.com</span>
      </p>
      <p class="email"><svg class="icon" viewBox="0 0 16 16" aria-hidden="true"><g fill="none" stroke="var(--ink)" stroke-width="1.3"><circle cx="8" cy="8" r="7"/><rect x="4" y="5.5" width="8" height="5.5"/><polyline points="4,5.5 8,8.5 12,5.5"/></g></svg>info@toviralanguagesf.com</p>
      <p class="address">Four Wexmoor Plaza, Lobby 3<br>San Francisco, CA 94187</p>
    </section>

    <svg class="bottom-wave" viewBox="0 0 420 110" preserveAspectRatio="none" aria-hidden="true">
      <path d="M0 62 Q210 48 420 0 L420 110 L0 110 Z" fill="var(--accent-yellow)"/>
      <path d="M0 70 Q220 56 420 6 L420 110 L0 110 Z" fill="var(--headline-red)"/>
      <path d="M0 80 Q230 66 420 20 L420 110 L0 110 Z" fill="var(--brand-green)"/>
    </svg>
  </main>
</body>
</html>
```